Powerpoint to present for client our social media services along with a test case

we need a powerpoint template design that is modern looking and eye catching and keeps the client engaged. we are a social media agency based in Kuwait so the content will be bilingual in english and in Arabic. i will be providing the logo and you can design based upon the logo provided. the main tasks for this PPT is to show case our case studies and for sales presentation. the presentations will be a mix of visuals, texts, graphs and charts.
the ppt design has to reflect the company colors in the logo with the logo scattered to show it is done by the company.

Industry/Entity Type

It Company

```html
<!DOCTYPE html>
<html lang="en">
<head>
<meta charset="utf-8">
<title>Sed et mi placerat odio auctor</title>
<link rel="stylesheet" href="https://fonts.googleapis.com/css2?family=Poppins:wght@500;600&family=Questrial&display=swap">
<style>
  :root {
    --magenta: #c8187e;
    --purple: #5a2a79;
    --green: #9dc93b;
    --maroon: #8e1138;
    --sidebar: #2c2a33;
    --ink: #111111;
    --muted: #8a8a8a;
    --rule: #3a3a3a;
    --grid: #d4d4d4;
    --bg: #f3f3f3;
  }
  * { margin: 0; padding: 0; box-sizing: border-box; }
  html, body { width: 1200px; height: 675px; overflow: hidden; }
  body {
    font-family: "Questrial", "Century Gothic", sans-serif;
    color: var(--ink);
    background: radial-gradient(ellipse at 60% 40%, #ffffff 0%, var(--bg) 75%);
    position: relative;
  }
  .slide { position: absolute; inset: 0; }
  .sidebar { position: absolute; left: 0; top: 0; width: 65px; height: 675px; background: var(--sidebar); }
  .graphics { position: absolute; left: 0; top: 0; width: 1200px; height: 675px; }
  .brand-name {
    position: absolute; left: 32px; top: 600px;
    transform: rotate(-90deg); transform-origin: left top;
    color: #ffffff; font-size: 17px; letter-spacing: 3px; white-space: nowrap;
    display: flex; align-items: center; gap: 8px;
  }
  .brand-dot { width: 12px; height: 12px; border-radius: 50%; background: var(--green); }
  .kicker { position: absolute; left: 146px; top: 43px; font-size: 12.5px; color: #555; letter-spacing: .2px; }
  .title { position: absolute; left: 144px; top: 64px; font-family: "Poppins", sans-serif; font-weight: 600; font-size: 42px; letter-spacing: -.5px; }
  .subtitle { position: absolute; left: 146px; top: 125px; font-size: 16px; }
  .legend { position: absolute; }
  .legend h2 { font-family: "Poppins", sans-serif; font-weight: 600; font-size: 20px; line-height: 26px; }
  .legend p.sub { font-size: 21px; line-height: 26px; margin-bottom: 14px; }
  .legend ul { list-style: none; }
  .legend li { position: relative; padding-left: 22px; font-size: 12px; color: var(--muted); line-height: 15px; margin-bottom: 7px; }
  .legend li::before { content: ""; position: absolute; left: 2px; top: 3px; width: 10px; height: 10px; border-radius: 50%; background: var(--c); }
  .legend-left { left: 409px; top: 201px; }
  .legend-right { left: 957px; top: 201px; }
  .notes { position: absolute; top: 513px; border-top: 1px solid var(--rule); padding-top: 13px; list-style: none; }
  .notes li { position: relative; padding-left: 22px; font-size: 13px; line-height: 19px; }
  .notes li::before { content: ""; position: absolute; left: 2px; top: 6px; width: 6px; height: 6px; background: var(--ink); }
  .notes-left { left: 144px; width: 446px; }
  .notes-right { left: 665px; width: 472px; }
  .footer { position: absolute; right: 105px; top: 606px; text-align: right; font-size: 14px; line-height: 17px; }
  .footer .date { font-family: "Poppins", sans-serif; font-weight: 500; }
  .footer .url { color: #555; }
  .page-divider { position: absolute; left: 1110px; top: 608px; width: 1px; height: 32px; background: #999; }
  .page-number { position: absolute; left: 1119px; top: 598px; font-family: "Poppins", sans-serif; font-weight: 600; font-size: 34px; color: #444; }
</style>
</head>
<body>
<div class="slide">
  <div class="sidebar"></div>

  <svg class="graphics" viewBox="0 0 960 540" xmlns="http://www.w3.org/2000/svg">
    <!-- corner accents -->
    <polygon points="0,0 95,0 0,22" fill="var(--magenta)"/>
    <polygon points="0,22 52,10 52,55" fill="var(--maroon)"/>
    <polygon points="52,10 52,100 66,55" fill="var(--green)"/>
    <polygon points="0,22 0,70 52,55" fill="#6d0f2e"/>

    <!-- donut chart -->
    <g class="donut" transform="translate(227 270)">
      <path d="M0,-110 A110,110 0 1 0 95.3,55 L69.3,40 A80,80 0 1 1 0,-80 Z" fill="var(--magenta)"/>
      <path d="M0,-80 A80,80 0 1 0 40,69.3 L27.5,47.6 A55,55 0 1 1 0,-55 Z" fill="var(--purple)"/>
      <path d="M0,-97 A97,97 0 0 1 48.5,84 L27.5,47.6 A55,55 0 0 0 0,-55 Z" fill="var(--green)"/>
      <circle r="57" fill="#ffffff"/>
      <g class="group-icon" fill="#111">
        <circle cx="0" cy="-16" r="6"/>
        <rect x="-7" y="-8" width="14" height="30" rx="3"/>
        <circle cx="-14" cy="-10" r="4.5"/>
        <rect x="-20" y="-4" width="10" height="22" rx="3"/>
        <circle cx="14" cy="-10" r="4.5"/>
        <rect x="10" y="-4" width="10" height="22" rx="3"/>
      </g>
      <text x="-95" y="0" transform="rotate(-90 -95 0)" text-anchor="middle" font-family="Poppins, sans-serif" font-weight="600" font-size="14" fill="#fff">76%</text>
      <text x="-67" y="0" transform="rotate(-90 -67 0)" text-anchor="middle" font-family="Poppins, sans-serif" font-weight="600" font-size="14" fill="#fff">76%</text>
      <text x="60" y="-22" text-anchor="middle" font-family="Poppins, sans-serif" font-weight="600" font-size="14" fill="#222">76%</text>
    </g>

    <!-- area chart -->
    <g class="area-chart" font-family="Questrial, sans-serif" font-size="10">
      <g stroke="var(--grid)" stroke-width="1">
        <line x1="535" y1="187" x2="742" y2="187"/>
        <line x1="535" y1="232" x2="742" y2="232"/>
        <line x1="535" y1="278" x2="742" y2="278"/>
        <line x1="535" y1="323" x2="742" y2="323"/>
        <line x1="535" y1="369" x2="742" y2="369"/>
      </g>
      <polygon points="535,187 597,259 635,282 675,290 742,260 742,369 535,369" fill="var(--green)"/>
      <polygon points="535,228 570,265 597,282 668,280 705,325 705,369 535,369" fill="var(--purple)"/>
      <polygon points="535,228 597,300 668,326 742,324 742,369 535,369" fill="var(--magenta)"/>
      <g fill="#222" text-anchor="end">
        <text x="528" y="191">10</text>
        <text x="528" y="236">9</text>
        <text x="528" y="282">8</text>
        <text x="528" y="327">7</text>
        <text x="528" y="373">6</text>
      </g>
      <g fill="#222" font-family="Poppins, sans-serif" font-weight="600" font-size="9.5" text-anchor="middle">
        <text x="546" y="384">2011</text>
        <text x="609" y="384">2012</text>
        <text x="668" y="384">2013</text>
        <text x="731" y="384">2014</text>
      </g>
    </g>
  </svg>

  <div class="brand-name"><span class="brand-dot"></span>NOVA SOCIAL</div>

  <p class="kicker">BUILDING BRANDS THROUGH COMMUNITIES</p>
  <h1 class="title">Sed et mi placerat odio auctor</h1>
  <p class="subtitle">Aenean dictum tortor euismod magna faucibus, tincidunt&nbsp; congue</p>

  <div class="legend legend-left">
    <h2>Euismod</h2>
    <p class="sub">magna faucibus</p>
    <ul>
      <li style="--c: var(--magenta)">Maecenas scelerisque</li>
      <li style="--c: var(--purple)">Pellentesque</li>
      <li style="--c: var(--green)">Fusce et turpis euismod<br>placerat tellus</li>
    </ul>
  </div>

  <div class="legend legend-right">
    <h2>Curabitur</h2>
    <p class="sub">Curabitur vene</p>
    <ul>
      <li style="--c: var(--magenta)">Maecenas scelerisque</li>
      <li style="--c: var(--purple)">Pellentesque</li>
      <li style="--c: var(--green)">Fusce et turpis euismod<br>placerat tellus</li>
    </ul>
  </div>

  <ul class="notes notes-left">
    <li>Create a strategy for the entire Share service</li>
    <li>Divide TeamPortal into solutions business users can relate to</li>
  </ul>
  <ul class="notes notes-right">
    <li>Create a strategy for the entire Share service</li>
    <li>Divide TeamPortal into solutions business users can relate to</li>
  </ul>

  <div class="footer">
    <div class="date">March 24, 2014</div>
    <div class="url">www.novasocial.com</div>
  </div>
  <div class="page-divider"></div>
  <div class="page-number">7</div>
</div>
</body>
</html>
```